Maplecrest Cove Retreat Wedding and Event Venue

We are looking for a webpage for our Wedding and Event Venue just opened up in Eastern San Diego CA. It is out of a private home that has a very photogenic backyard including grapevines and orchard trees, a 15 ft waterfall into a pool and market lights hanging from trees, all connected by paved stone and compacted dirt paths

We are looking for something that will be very bright, warm and inviting to our clients. The clientele will be mostly couples between 22 and 35 years of age for the weddings and planners/executives age 22-60 for our corporate events.

We would like a rustic Outdoor look as that is what our venue showcases. You can see our facebook Here: https://www.facebook.com/MaplecrestCoveRetreat/

We would like for the pictures on the facebook to be used on the page. The google drive where most of them are located is here for full file sizes https://files.examplecloud.net/open?id=7Q-9Kpt-M2xvaT8LwQeRTp4-DN5H

We would like to see designs that go with the colors of our logo and that included stone, wood, and grapevine textures as well as anything else rustic such as Market-lights.

The final design should be welcoming for newly engaged couples and corporations/companies who would like to book an outdoor venue for their wedding or next event. There can even be a simple first page with separate tabs for weddings and events that will be able to be more specially focused to the clients.

We would also like the option to be able to edit the pictures we place on the site seasonally as we would like our pictures to reflect our clients

Target Market(s)

Engaged couples age 22-35 and corporate planners/executives age 22-60

Industry/Entity Type

Events

Font styles to use
Script

Requirements
Must have
• Rustic Look, (wood, stone, wine vines/barrels, market lights, mason jars, etc)
• tab pages/sub pages for "About us", "Packages", "Pricing", "Gallery" (we must be able to put our pictures here from all our events), "What makes us Unique", "Contact us" that we are able to enter information into
Nice to have
• Colors matching our logo, Pictures from our Facebook page (listed in brief)
Should not have
• Corporate Look

```html
<!DOCTYPE html>
<html lang="en">
<head>
<meta charset="utf-8">
<title>Maplecrest Cove Retreat Wedding and Event Venue</title>
<link rel="stylesheet" href="https://fonts.googleapis.com/css2?family=Cinzel:wght@400;700&family=Open+Sans:wght@400;600&display=swap">
<style>
:root{
  --wood-deep:#1e0f08;
  --wood:#3b2215;
  --wood-warm:#5a3520;
  --gold:#c9a75f;
  --gold-soft:#d8bd7e;
  --gold-band:#b99d5a;
  --ink-light:#eadfcc;
  --ink-muted:#cbbba3;
  --ink-dark:#5d5548;
  --cream:#f4eee4;
  --white:#ffffff;
}
*{box-sizing:border-box;margin:0;padding:0}
html,body{width:1200px;height:4276px;overflow:hidden}
body{font-family:"Open Sans",Arial,sans-serif;color:var(--ink-light);background:var(--wood-deep)}
.section{position:relative;width:1200px;overflow:hidden}
.wood{background:
  linear-gradient(90deg,rgba(0,0,0,.35),rgba(0,0,0,0) 20%,rgba(0,0,0,0) 80%,rgba(0,0,0,.35)),
  linear-gradient(180deg,#3a2114,#2b170d 45%,#3d2416 70%,#24130a)}
.photo{position:absolute;display:block}
.heading{font-family:"Cinzel",Georgia,serif;font-weight:400;color:var(--gold);letter-spacing:1px;text-transform:uppercase}
.body-text{font-size:12.5px;line-height:23px;color:var(--ink-light)}
.btn{position:absolute;display:flex;align-items:center;justify-content:center;width:124px;height:38px;border:1.5px solid var(--gold);border-radius:20px;color:var(--ink-light);font-size:13px;text-decoration:none}

/* header */
.site-header{height:180px}
.brand{position:absolute;left:500px;top:32px;width:200px;text-align:center;color:var(--gold);font-family:"Cinzel",Georgia,serif;font-weight:400}
.brand-mark{width:38px;height:38px;border:2px solid var(--gold);margin:0 auto 8px}
.brand-name{font-size:17px;line-height:20px;letter-spacing:1px}
.brand-sub{font-size:10px;letter-spacing:5px;margin-top:2px}
.main-nav{position:absolute;top:118px;left:100px;width:1000px;display:flex;justify-content:space-between;font-size:12.5px;text-transform:uppercase;letter-spacing:.5px}
.main-nav .group{display:flex;gap:46px}
.main-nav a{color:var(--white);text-decoration:none}
.nav-rule{position:absolute;left:86px;right:86px;top:152px;height:1px;background:rgba(201,167,95,.35)}

/* hero */
.hero{height:475px}
.hero-photo{left:0;top:0;width:1200px;height:475px;background:linear-gradient(100deg,#d8c3a6 0%,#f3e9dc 28%,#fbf6ee 48%,#e9d6bf 70%,#c9a888 100%)}
.hero-caption{position:absolute;left:0;top:405px;width:1200px;height:70px;background:rgba(40,24,14,.75);display:flex;align-items:center;justify-content:center}
.hero-caption h1{font-size:30px;color:var(--white)}
.arrow{position:absolute;width:46px;height:46px}

/* welcome */
.welcome{height:577px}
.title-row{position:absolute;left:0;width:1200px;display:flex;align-items:center;justify-content:center;gap:22px}
.title-row .rule{width:74px;height:1px;background:var(--gold)}
.title-row h2{font-size:25px}
.card{position:absolute;top:135px;width:328px}
.card .photo{position:relative;width:328px;height:202px}
.card h3{margin-top:26px;font-size:18px;font-weight:600;color:var(--gold)}
.card p{margin-top:10px;font-size:12px;line-height:22px}
.card .btn{position:relative;margin-top:20px}

/* venue band */
.venue{height:358px;background:linear-gradient(90deg,#efe5d6,#f6f1e9 55%,#efe8dc)}
.venue-photo{left:0;top:0;width:613px;height:358px;background:linear-gradient(110deg,#cbb397,#ede0cd 40%,#f7efe4 70%,#e2cfb8)}
.venue-copy{position:absolute;left:640px;top:72px;width:500px;text-align:center}
.venue-copy h2{font-size:24px;color:var(--gold)}
.venue-copy p{margin-top:42px;font-size:12px;line-height:23px;color:var(--ink-dark)}
.venue-copy .btn{position:relative;margin:40px auto 0;color:var(--ink-dark)}

/* split sections */
.unique{height:382px;background:linear-gradient(180deg,#140a05,#1d0f08)}
.split-copy{position:absolute;left:86px;width:520px}
.split-copy h2{font-size:25px}
.split-copy p{margin-top:24px;font-size:12px;line-height:23px}
.split-copy .btn{position:relative;margin-top:30px}
.split-photo{left:656px;width:456px;height:284px}
.slide-dot{position:absolute;width:26px;height:26px}

.upcoming{height:359px}
.upcoming-photo{left:0;top:0;width:1200px;height:359px;background:linear-gradient(90deg,#5e6e66 0%,#b9c5c0 18%,#c9d1cd 40%,#a9b7b3 100%)}
.upcoming-copy{position:absolute;left:610px;top:70px;width:460px;text-align:center}
.upcoming-copy h2{font-size:24px;color:var(--white)}
.upcoming-copy p{margin-top:38px;font-size:12px;line-height:23px;color:var(--white)}
.upcoming-copy .btn{position:relative;margin:22px auto 0;border-color:var(--white);color:var(--white)}

.pricing{height:371px}

/* about */
.about{height:362px;background:linear-gradient(90deg,#a88c4c,var(--gold-band) 30%,#c2a765 60%,#ab8f4f)}
.about-copy{position:absolute;left:200px;top:90px;width:800px;text-align:center}
.about-copy h2{font-size:24px;color:var(--white)}
.about-copy p{margin-top:40px;font-size:12px;line-height:23px;color:var(--white)}
.about-copy .btn{position:relative;margin:18px auto 0;border-color:var(--white);color:var(--white)}

/* subscribe */
.subscribe{height:926px}
.subscribe-copy{position:absolute;left:200px;top:40px;width:800px;text-align:center}
.subscribe-copy h2{font-size:24px}
.subscribe-copy p{margin-top:20px;font-size:12px;line-height:23px}
.signup{position:absolute;left:285px;top:165px;width:627px;height:49px;display:flex}
.signup .field{flex:1;background:var(--white);color:#777;font-size:12px;display:flex;align-items:center;padding-left:16px}
.signup .submit{width:148px;background:var(--gold);color:var(--white);font-size:13px;font-weight:600;display:flex;align-items:center;justify-content:center;letter-spacing:1px}

/* footer */
.site-footer{height:286px;background:var(--gold-band)}
.site-footer .brand{top:28px;color:var(--white)}
.site-footer .brand-mark{border-color:var(--white)}
.footer-nav{position:absolute;top:188px;left:0;width:1200px;display:flex;justify-content:center;gap:20px;font-size:12px;text-transform:uppercase;color:var(--white)}
.footer-nav a{color:var(--white);text-decoration:none}
.copyright{position:absolute;top:234px;width:1200px;text-align:center;font-size:11px;color:var(--white)}
</style>
</head>
<body>

<header class="section site-header wood">
  <div class="brand">
    <div class="brand-mark"></div>
    <div class="brand-name">MAPLECREST COVE</div>
    <div class="brand-sub">RETREAT</div>
  </div>
  <nav class="main-nav">
    <div class="group"><a href="#">Home</a><a href="#">About Us</a><a href="#">Packages</a><a href="#">Pricing</a></div>
    <div class="group"><a href="#">Gallery</a><a href="#">What Makes Us Unique</a><a href="#">Contact Us</a></div>
  </nav>
  <div class="nav-rule"></div>
</header>

<section class="section hero">
  <div class="photo hero-photo" role="img" aria-label="Bride in a white gown having her veil adjusted by a bridesmaid in a sunlit room"></div>
  <div class="hero-caption">
    <svg class="arrow" style="left:98px;top:12px" viewBox="0 0 46 46"><circle cx="23" cy="23" r="21" fill="none" stroke="#fff" stroke-width="2"/><path d="M26 15l-8 8 8 8" fill="none" stroke="#fff" stroke-width="2.5"/></svg>
    <h1 class="heading">Wedding &amp; Event Venue</h1>
    <svg class="arrow" style="left:1055px;top:12px" viewBox="0 0 46 46"><circle cx="23" cy="23" r="21" fill="none" stroke="#fff" stroke-width="2"/><path d="M20 15l8 8-8 8" fill="none" stroke="#fff" stroke-width="2.5"/></svg>
  </div>
</section>

<section class="section welcome wood">
  <div class="title-row" style="top:48px"><span class="rule"></span><h2 class="heading">Welcome to Maplecrest Cove</h2><span class="rule"></span></div>
  <article class="card" style="left:86px">
    <div class="photo" role="img" aria-label="Bride and her mother getting ready together" style="background:linear-gradient(120deg,#d9c6ad,#f2e8da 50%,#c7ab8c)"></div>
    <h3>15 ft waterfall into a pool</h3>
    <p>Guests gather by the falls for toasts, photos and quiet talks as the warm evening light settles over the garden.</p>
    <a class="btn" href="#">Read More</a>
  </article>
  <article class="card" style="left:436px">
    <div class="photo" role="img" aria-label="Bridesmaids in red helping the bride with her gown" style="background:linear-gradient(120deg,#c9b7a1,#efe4d6 45%,#b86a5c 80%,#d9c8b4)"></div>
    <h3>Market Lights</h3>
    <p>Strings of soft bulbs glow above the paths, turning the garden into a warm open room for dinner and dancing.</p>
    <a class="btn" href="#">Read More</a>
  </article>
  <article class="card" style="left:787px">
    <div class="photo" role="img" aria-label="Bride putting on her earrings" style="background:linear-gradient(120deg,#b99874,#e8d6bf 50%,#c39d78)"></div>
    <h3>Hanging From Trees</h3>
    <p>Lights drape from old orchard branches, giving every table a gentle glow that lasts long after the sun goes down.</p>
    <a class="btn" href="#">Read More</a>
  </article>
</section>

<section class="section venue">
  <div class="photo venue-photo" role="img" aria-label="Mother of the bride fixing the bride's veil"></div>
  <div class="venue-copy">
    <h2 class="heading">Wedding &amp; Event Venue</h2>
    <p>Our private backyard hosts weddings and company events among grapevines, orchard trees and stone paths lit for the night.</p>
    <a class="btn" href="#">Read More</a>
  </div>
</section>

<section class="section unique">
  <div class="split-copy" style="top:94px">
    <h2 class="heading">What Makes Us Unique</h2>
    <p>Every event here takes place in a family home surrounded by vines, fruit trees and a waterfall pool. Couples and planners shape the day their way, with open lawns for ceremonies, shaded corners for dinner and paths that lead guests from one setting to the next under a canopy of lights.</p>
    <a class="btn" href="#">Read More</a>
  </div>
  <div class="photo split-photo" style="top:52px;background:linear-gradient(90deg,#8e1f22,#b8383a 30%,#d8c9bb 50%,#b4393a 75%,#7f1c1f)" role="img" aria-label="Bride with family in front of a rack of red bridesmaid dresses"></div>
  <svg class="slide-dot" style="left:662px;top:181px" viewBox="0 0 26 26"><circle cx="13" cy="13" r="11" fill="rgba(0,0,0,.35)" stroke="#fff" stroke-width="1.5"/><path d="M15 8l-5 5 5 5" fill="none" stroke="#fff" stroke-width="2"/></svg>
  <svg class="slide-dot" style="left:1080px;top:181px" viewBox="0 0 26 26"><circle cx="13" cy="13" r="11" fill="rgba(0,0,0,.35)" stroke="#fff" stroke-width="1.5"/><path d="M11 8l5 5-5 5" fill="none" stroke="#fff" stroke-width="2"/></svg>
</section>

<section class="section upcoming">
  <div class="photo upcoming-photo" role="img" aria-label="Groom in a white shirt fastening his collar by a window"></div>
  <div class="upcoming-copy">
    <h2 class="heading">Upcoming Events</h2>
    <p>See the open dates for the season ahead and join us for tours, tastings and garden evenings at the venue.</p>
    <a class="btn" href="#">Read More</a>
  </div>
</section>

<section class="section pricing wood">
  <div class="split-copy" style="top:82px">
    <h2 class="heading">Our Pricing</h2>
    <p>Packages cover the garden, tables, lights and setup for groups large and small. Choose a half day for a company gathering or a full weekend for a wedding, then add catering, music and rentals as you need them. Ask us for a quote and we will reply within two days.</p>
    <a class="btn" href="#">Read More</a>
  </div>
  <div class="photo split-photo" style="top:40px;height:285px;background:linear-gradient(110deg,#d6c3a9,#f3eadd 45%,#fbf7f0 65%,#d8c2a5)" role="img" aria-label="Bridesmaid adjusting the bride's veil"></div>
</section>

<section class="section about">
  <div class="photo" style="left:0;top:0;width:1200px;height:362px;opacity:.18;background:linear-gradient(90deg,#6b5430,#e6d3a6 30%,#6b5430 55%,#e6d3a6 80%,#6b5430)" role="img" aria-label="Faded photos of the bridal party smiling"></div>
  <div class="about-copy">
    <h2 class="heading">About Wedding &amp; Event</h2>
    <p>We opened our home to share its garden with couples and teams who want a warm, relaxed place to celebrate together.</p>
    <a class="btn" href="#">Read More</a>
  </div>
</section>

<section class="section subscribe wood">
  <div class="subscribe-copy">
    <h2 class="heading">Our Subscribe</h2>
    <p>Sign up for news on open dates, seasonal offers and new photos from recent events in the garden, sent once a month.</p>
  </div>
  <form class="signup">
    <div class="field">Enter Your Email Id :</div>
    <div class="submit">SUBSCRIBE</div>
  </form>
  <div class="photo" style="left:86px;top:262px;width:507px;height:294px;background:linear-gradient(120deg,#cdb6a6,#f1e3de 50%,#d6b8b0)" role="img" aria-label="Bride and bridesmaids in robes sitting on a bed"></div>
  <div class="photo" style="left:604px;top:262px;width:245px;height:294px;background:linear-gradient(120deg,#6e6a66,#c9c2b8 50%,#4f4d4a)" role="img" aria-label="Groom and father in vests"></div>
  <div class="photo" style="left:861px;top:262px;width:253px;height:294px;background:linear-gradient(120deg,#e9e4dc,#faf8f3 50%,#d9d2c6)" role="img" aria-label="Wedding dress hanging by a window"></div>
  <div class="photo" style="left:86px;top:570px;width:250px;height:299px;background:linear-gradient(120deg,#3e3836,#e8e1d8 55%,#b8aa9a)" role="img" aria-label="Bride hugging the groom"></div>
  <div class="photo" style="left:348px;top:570px;width:245px;height:299px;background:linear-gradient(120deg,#e6e2da,#f7f4ee 50%,#8fa2a4)" role="img" aria-label="Hand holding a pair of blue sneakers"></div>
  <div class="photo" style="left:604px;top:570px;width:510px;height:299px;background:linear-gradient(120deg,#3a2a24,#8a2a2c 45%,#c89a84 70%,#4a342c)" role="img" aria-label="Bridesmaid in red helping another with her hair"></div>
</section>

<footer class="section site-footer">
  <div class="brand">
    <div class="brand-mark"></div>
    <div class="brand-name">MAPLECREST COVE</div>
    <div class="brand-sub">RETREAT</div>
  </div>
  <nav class="footer-nav">
    <a href="#">Home</a><span>|</span><a href="#">About Us</a><span>|</span><a href="#">Packages</a><span>|</span><a href="#">Pricing</a><span>|</span><a href="#">Gallery</a><span>|</span><a href="#">What Makes Us Unique</a><span>|</span><a href="#">Contact Us</a>
  </nav>
  <p class="copyright">© Copyright 2017 Maplecrest Cove. All Rights Reserved</p>
</footer>

</body>
</html>
```